Business Card Design

We need a business card designed for our new company. Prefer a black card with white logo & writing.

Contact Information for Business Card

Ted Galloway, address: 7-4812 Fernhollow Road, Abbotsford, BC, V3K 8R2, Office Phone: 604-712-3390, Cell: 604-947-2164, Email: ted@resinworkshub.ca

Colors

Designer to choose only greyscale colors for use in the design.

```html
<!DOCTYPE html>
<html lang="en">
<head>
<meta charset="utf-8">
<title>Resin Works Hub – Business Card</title>
<link href="https://fonts.googleapis.com/css2?family=Poppins:wght@400;600&display=swap" rel="stylesheet">
<style>
  :root {
    --backdrop: #b7b7b7;
    --card-black: #000000;
    --card-panel: #0c0c0c;
    --ink-white: #ffffff;
    --rule-grey: #6a6a6a;
    --faint-grey: #141414;
  }
  html, body {
    margin: 0;
    width: 1200px;
    height: 1200px;
    overflow: hidden;
    background: var(--backdrop);
    font-family: "Poppins", sans-serif;
  }
  .canvas { position: relative; width: 1200px; height: 1200px; }
  .card {
    position: absolute;
    top: 303px;
    width: 368px;
    height: 594px;
    background: var(--card-black);
    color: var(--ink-white);
    overflow: hidden;
  }
  .card--front {
    left: 200px;
    background: radial-gradient(ellipse at 50% 85%, var(--faint-grey) 0%, var(--card-black) 70%);
  }
  .card--back { left: 599px; width: 365px; }
  .wordmark {
    position: absolute;
    left: 0; right: 0;
    text-align: center;
    font-weight: 600;
    line-height: 1;
    color: var(--ink-white);
  }
  .wordmark__main { display: block; font-size: 38px; letter-spacing: 0.5px; }
  .wordmark__sub { display: block; font-size: 17px; letter-spacing: 9px; margin-top: 12px; padding-left: 9px; }
  .card--front .wordmark { top: 410px; }
  .card--back .wordmark { top: 132px; }
  .back-panel {
    position: absolute;
    left: 0; right: 0; top: 311px; bottom: 0;
    background: var(--card-panel);
  }
  .back-panel__notch {
    position: absolute;
    top: 0; left: 50%;
    width: 0; height: 0;
    margin-left: -7px;
    border-left: 7px solid transparent;
    border-right: 7px solid transparent;
    border-top: 7px solid var(--card-black);
  }
  .contact {
    position: absolute;
    left: 0; right: 0; top: 0;
    text-align: center;
  }
  .contact__name {
    position: absolute; left: 0; right: 0; top: 36px;
    margin: 0; font-size: 24px; font-weight: 600; letter-spacing: 0.3px;
  }
  .contact__icons {
    position: absolute; left: 0; right: 0; top: 84px;
    display: flex; justify-content: center; align-items: center; gap: 5px;
  }
  .contact__icons .rule { width: 52px; height: 1px; background: var(--rule-grey); margin: 0 4px; }
  .icon-tile {
    width: 25px; height: 25px; border-radius: 3px;
    background: var(--ink-white);
    display: flex; align-items: center; justify-content: center;
  }
  .contact__lines {
    position: absolute; left: 0; right: 0; top: 120px;
    font-size: 17px; line-height: 21.5px;
  }
  .contact__divider {
    position: absolute; left: 88px; right: 80px; top: 196px;
    height: 1px; background: var(--rule-grey);
  }
  .contact__address {
    position: absolute; left: 0; right: 0; top: 210px;
    font-size: 17px; line-height: 22px;
  }
  .contact p { margin: 0; }
</style>
</head>
<body>
<main class="canvas">
  <section class="card card--front" aria-label="Card front">
    <div class="wordmark">
      <span class="wordmark__main">RESIN WORKS</span>
      <span class="wordmark__sub">HUB</span>
    </div>
  </section>

  <section class="card card--back" aria-label="Card back">
    <div class="wordmark">
      <span class="wordmark__main">RESIN WORKS</span>
      <span class="wordmark__sub">HUB</span>
    </div>
    <div class="back-panel">
      <div class="back-panel__notch"></div>
      <div class="contact">
        <h1 class="contact__name">TED GALLOWAY</h1>
        <div class="contact__icons">
          <span class="rule"></span>
          <span class="icon-tile" aria-label="Office phone">
            <svg width="16" height="16" viewBox="0 0 16 16"><path d="M2 6c0-2 3-3 6-3s6 1 6 3v1h-3V5.5H5V7H2z M4 8h8l1 5H3z" fill="#000"/></svg>
          </span>
          <span class="icon-tile" aria-label="Mobile">
            <svg width="16" height="16" viewBox="0 0 16 16"><rect x="4.5" y="1.5" width="7" height="13" rx="1" fill="none" stroke="#000" stroke-width="1.4"/><circle cx="8" cy="12.3" r="0.8" fill="#000"/></svg>
          </span>
          <span class="icon-tile" aria-label="Email">
            <svg width="16" height="16" viewBox="0 0 16 16"><rect x="2" y="4" width="12" height="8.5" fill="none" stroke="#000" stroke-width="1.3"/><path d="M2 4l6 5 6-5" fill="none" stroke="#000" stroke-width="1.3"/></svg>
          </span>
          <span class="rule"></span>
        </div>
        <div class="contact__lines">
          <p>604-712-3390</p>
          <p>604-947-2164</p>
          <p>ted@resinworkshub.ca</p>
        </div>
        <div class="contact__divider"></div>
        <div class="contact__address">
          <p>7-4812 Fernhollow Road</p>
          <p>Abbotsford, BC, V3K 8R2</p>
        </div>
      </div>
    </div>
  </section>
</main>
</body>
</html>
```